Association qui souhaite améliorer l'accès aux personnes en situation de handicap

Nous sommes une association qui a pour objectif d'améliorer l'accessibilité, augmenter l'offre des activités réalisables dans notre région touristique.
Nous souhaitons réaliser un site internet afin de pouvoir communiquer sur notre association. Nous avons déjà conçu notre flyer sur Plumotrix. Nous souhaiterions une base graphique se rapportant à celui-ci. C'est possible de tout retravailler mais nous souhaitons tout de même retrouver la charte graphique ou code couleur du flyer.
Il nous faudrait quelques pages:
- 1 page : Acceuil / Présentation (Home), Il y aurait le descriptif de l'association, avec ses objectifs à +/- moyen terme
- 1 page : Nos réalisations, celle-ci présenterait les éléments que nous avons réalisés avec des zones de textes et des images classées chronologiquement au fur et à mesure des nouveautés
- 1 page : Media, comme la précédente, mais ou on pourrait voir ou lire sur les divers médias qui parlent de nous
- 1 page : Evenements : c'est une page pour présenter divers activités que nous allons organiser
- 1 page : Contact qui indique comment nous contacter et avec la présentation des 5 ou 6 membres du comité
- 1 link donate : qui arrive sur un formulaire de donnée que l'on pourra faire évoluer sur un système de payement par la suite. Cette bannière doit se retrouver sur toutes les pages
Il est nécessaire que se design puisse être transféré sur une lecture sur téléphone mobile
Personnes en situation de handicap
Associatif

```html
<!DOCTYPE html>
<html lang="en">
<head>
<meta charset="utf-8">
<title>Open Paths Association</title>
<link href="https://fonts.googleapis.com/css2?family=Bebas+Neue&family=Mulish:wght@400;600;700&family=Raleway:wght@500;600;700&display=swap" rel="stylesheet">
<style>
:root{
  --red:#c0172a;
  --red-bright:#e3202f;
  --ink:#1f2226;
  --text:#4a4d52;
  --dark:#2a2e33;
  --cream:#fcfbf5;
  --white:#ffffff;
  --line:#8a8d92;
}
*{margin:0;padding:0;box-sizing:border-box}
html,body{width:1200px;height:3333px;overflow:hidden}
body{position:relative;background:var(--white);font-family:'Mulish',sans-serif;color:var(--text)}
.abs{position:absolute}
.display{font-family:'Raleway',sans-serif;font-weight:600;color:var(--ink)}
.condensed{font-family:'Bebas Neue',sans-serif;letter-spacing:.5px}
.btn{position:absolute;display:flex;align-items:center;justify-content:center;background:var(--red);color:var(--white);border-radius:22px;font-size:11.5px;font-weight:700;text-transform:uppercase;letter-spacing:.3px}
.btn-readmore{width:117px;height:39px}
.wordmark{display:flex;align-items:center;gap:7px;font-family:'Mulish',sans-serif;font-weight:700;font-size:12.5px;line-height:1.05;letter-spacing:.4px;text-transform:uppercase}
.wordmark .mark{width:20px;height:20px;background:var(--red)}

/* top bar */
.topbar{left:0;top:0;width:1200px;height:28px;background:var(--red);color:var(--white);font-size:11px}
.topbar .social-dot{position:absolute;left:129px;top:8px;width:12px;height:12px;border-radius:50%;background:var(--white)}
.topbar .mail{position:absolute;right:128px;top:7px;display:flex;align-items:center;gap:6px}

/* nav */
.nav{left:0;top:28px;width:1200px;height:62px;background:var(--white)}
.nav .wordmark{position:absolute;left:130px;top:14px;color:var(--ink)}
.nav-links{position:absolute;top:25px;font-size:11px;color:var(--ink)}
.nav-links span{position:absolute;white-space:nowrap}
.nav-home{color:var(--red)}
.donate{left:977px;top:45px;width:94px;height:30px;border-radius:16px;font-size:11.5px}

/* hero */
.hero{left:0;top:90px;width:1200px;height:442px;background:linear-gradient(100deg,#1c2a24 0%,#3c4c43 35%,#6d7a72 60%,#98a29c 80%,#5d6863 100%)}
.hero-kicker{left:130px;top:210px;font-size:30px;color:var(--white)}
.hero-title{left:130px;top:240px;font-family:'Raleway',sans-serif;font-weight:700;font-size:44px;color:var(--white);letter-spacing:.3px}
.hero-title em{font-style:normal;color:var(--red-bright)}
.hero-text{left:130px;top:306px;width:430px;font-size:13px;line-height:19.5px;color:var(--white)}
.dots{left:130px;top:498px;display:flex;gap:12px}
.dots i{width:10px;height:10px;border-radius:50%;background:var(--white)}
.dots i.on{background:var(--red-bright)}

/* welcome */
.welcome-kicker{left:611px;top:637px;font-size:19px;color:var(--ink)}
.welcome-title{left:611px;top:665px;font-size:35px;font-weight:500}
.welcome-title em{font-style:normal;color:var(--red)}
.body-copy{font-size:12.8px;line-height:19.5px}
.welcome-text{left:611px;top:727px;width:460px}

/* achievements */
.achievements{left:0;top:1032px;width:1200px;height:515px}
.ach-title{left:132px;top:1158px;font-size:35px;font-weight:500;color:var(--white)}
.ach-text{left:132px;top:1224px;width:460px;color:#e6e8ea}

/* media */
.section-title{width:1200px;left:0;text-align:center;font-size:35px;font-weight:500}
.section-sub{width:1200px;left:0;text-align:center;font-size:13px}
.media-card{position:absolute;top:1700px;width:301px;height:202px}
.media-photo{position:absolute;left:0;top:0;width:301px;height:180px}
.media-label{position:absolute;left:27px;top:160px;width:247px;height:42px;background:var(--white);box-shadow:0 3px 10px rgba(0,0,0,.12);display:flex;align-items:center;justify-content:center;gap:6px;font-size:13px;color:var(--ink)}
.media-label b{color:var(--red);font-size:16px}

/* events */
.events{left:0;top:1968px;width:1200px;height:569px;background:linear-gradient(160deg,#3b4047 0%,#2b3036 45%,#353a40 100%)}
.event-card{position:absolute;top:2096px;width:301px;height:370px;background:var(--white)}
.event-photo{position:absolute;left:0;top:0;width:301px;height:208px}
.event-date{position:absolute;left:14px;top:13px;width:36px;height:41px;background:var(--red);color:var(--white);font-size:9.5px;font-weight:700;text-align:center;line-height:12px;padding-top:9px}
.event-title{position:absolute;left:22px;top:225px;font-size:15.5px;font-weight:600}
.event-text{position:absolute;left:23px;top:255px;width:260px;font-size:12.5px;line-height:19.5px}
.event-card .btn{left:24px;top:312px}

/* contact */
.contact{left:0;top:2537px;width:1200px;height:390px;background:var(--cream)}
.contact-title{left:531px;top:2643px;font-size:34px;font-weight:500}
.contact-sub{left:531px;top:2689px;font-size:13px;color:var(--ink)}
.field{position:absolute;border:1px solid var(--line);background:var(--white);font-size:10px;color:#666;padding:10px 9px}
.submit{position:absolute;left:764px;top:2839px;width:228px;height:35px;background:var(--red);color:var(--white);font-size:10.5px;display:flex;align-items:center;justify-content:center;letter-spacing:.3px}

/* footer */
.footer-text{color:#e0e2e4;font-size:10.5px}
.footer .wordmark{position:absolute;left:130px;top:3054px;color:var(--white);font-size:14px}
.footer-about{left:130px;top:3106px;width:210px;line-height:16px}
.footer-fb{left:130px;top:3176px;width:21px;height:21px;border-radius:50%;background:var(--red)}
.col-head{font-size:18px;color:var(--red-bright)}
.col-links{font-size:10.5px;color:#e0e2e4;line-height:22.6px}
.contact-row{position:absolute;left:876px;display:flex;gap:8px;align-items:flex-start;font-size:10.5px;color:#e0e2e4;line-height:14px}
.contact-row i{flex:none;width:21px;height:21px;border-radius:50%;border:1.5px solid var(--red);position:relative}
.contact-row i::after{content:"";position:absolute;left:6px;top:6px;width:6px;height:6px;border-radius:50%;background:var(--red)}
.copyright{left:0;top:3269px;width:1200px;text-align:center;font-size:10px;color:#e0e2e4}
.copyright span{color:var(--red-bright)}
</style>
</head>
<body>

<!-- top bar -->
<div class="abs topbar">
  <span class="social-dot" aria-label="Social page"></span>
  <div class="mail">
    <svg width="12" height="9" viewBox="0 0 12 9"><rect x=".5" y=".5" width="11" height="8" fill="none" stroke="#fff"/><path d="M.5 .5 6 5l5.5-4.5" fill="none" stroke="#fff"/></svg>
    info@openpaths-association.example
  </div>
</div>

<!-- navigation -->
<header class="abs nav">
  <div class="wordmark"><span class="mark"></span><span>Open Paths<br>Association</span></div>
</header>
<nav class="nav-links" style="left:0;top:53px;width:1200px;height:20px">
  <span class="nav-home" style="left:539px">Home</span>
  <span style="left:610px">Our Achievements</span>
  <span style="left:741px">Media</span>
  <span style="left:812px">Events</span>
  <span style="left:887px">Contacts</span>
</nav>
<svg class="abs" style="left:539px;top:68px" width="30" height="8" viewBox="0 0 30 8"><path d="M1 2l7 4 7-4 7 4 7-4" fill="none" stroke="#c0172a" stroke-width="1.6"/></svg>
<div class="btn donate">Donate</div>

<!-- hero -->
<section class="abs hero" role="img" aria-label="Photo of a woman in a wheelchair by a misty lake with a forest behind"></section>
<div class="abs condensed hero-kicker">Access the</div>
<h1 class="abs hero-title">TOURIST <em>REGION</em></h1>
<p class="abs hero-text">The resources of the association come from subscriptions, donations and events organized throughout the year.</p>
<div class="btn btn-readmore" style="left:130px;top:369px">Read more</div>
<div class="abs dots"><i class="on"></i><i></i><i></i></div>

<!-- welcome -->
<svg class="abs" style="left:100px;top:562px" width="440" height="412" viewBox="100 562 440 412">
  <polygon points="160,567 531,780 104,935" fill="#c0172a"/>
  <polygon points="130,597 528,782 130,968" fill="#6d8a4e" role="img" aria-label="Photo of a man with a white cane walking by a garden wall"/>
  <polygon points="130,597 528,782 130,968" fill="url(#wg)" opacity=".6"/>
  <defs><linearGradient id="wg" x1="0" x2="1"><stop offset="0" stop-color="#3f5a2e"/><stop offset=".5" stop-color="#e07a4a"/><stop offset="1" stop-color="#d8d6cc"/></linearGradient></defs>
</svg>
<div class="abs condensed welcome-kicker">Welcome to</div>
<h2 class="abs display welcome-title">Open <em>Paths</em> Association</h2>
<p class="abs body-copy welcome-text">Sed ut perspiciatis unde omnis iste natus error sit voluptatem accusantium doloremque laudantium, totam rem aperiam, eaque ipsa quae ab illo inventore veritatis et quasi architecto beatae vitae dicta sunt explicabo. Nemo enim ipsam voluptatem quia voluptas sit aspernatur aut odit aut fugit, sed quia consequuntur magni dolores eos qui ratione voluptatem sequi nesciunt.</p>
<div class="btn btn-readmore" style="left:611px;top:870px">Read more</div>

<!-- achievements -->
<svg class="abs achievements" viewBox="0 1032 1200 515" width="1200" height="515">
  <defs>
    <linearGradient id="ag" x1="0" y1="0" x2="1" y2="1"><stop offset="0" stop-color="#3a4645"/><stop offset=".6" stop-color="#2d3734"/><stop offset="1" stop-color="#1f2725"/></linearGradient>
    <linearGradient id="pg" x1="0" y1="0" x2="1" y2="1"><stop offset="0" stop-color="#5d6b4a"/><stop offset=".45" stop-color="#9bab6d"/><stop offset="1" stop-color="#3a3235"/></linearGradient>
  </defs>
  <rect x="0" y="1032" width="1200" height="515" fill="url(#ag)" role="img" aria-label="Dim photo of a person pushing a wheelchair across a mountain meadow"/>
  <polygon points="730,1032 1200,1032 1200,1547 1062,1547 595,1294" fill="#fff"/>
  <polygon points="741,1032 1200,1032 1200,1547 1077,1547 610,1294" fill="url(#pg)" role="img" aria-label="Photo of a hand touching tall grass beside a wheelchair wheel"/>
</svg>
<h2 class="abs display ach-title">Our Achievements</h2>
<p class="abs body-copy ach-text">Sed ut perspiciatis unde omnis iste natus error sit voluptatem accusantium doloremque laudantium, totam rem aperiam, eaque ipsa quae ab illo inventore veritatis et quasi architecto beatae vitae dicta sunt explicabo. Nemo enim ipsam voluptatem quia voluptas sit aspernatur aut odit aut fugit, sed quia consequuntur magni dolores eos qui ratione voluptatem sequi nesciunt.</p>
<div class="btn btn-readmore" style="left:132px;top:1373px">Read more</div>

<!-- media -->
<h2 class="abs display section-title" style="top:1604px">Our Media</h2>
<p class="abs section-sub" style="top:1652px">Sed ut perspiciatis unde omnis iste natus error sit voluptatem</p>
<div class="media-card" style="left:130px">
  <div class="media-photo" role="img" aria-label="Photo of a volunteer holding hands with an elderly woman outdoors" style="background:linear-gradient(120deg,#3e6a2c,#8fae6a 55%,#d9dfd6)"></div>
  <div class="media-label">Voluptas Sit Aspernatur <b>+</b></div>
</div>
<div class="media-card" style="left:449px">
  <div class="media-photo" role="img" aria-label="Photo of people helping someone in the snow" style="background:linear-gradient(120deg,#c9ccd0,#eef0f2 45%,#6b6f78)"></div>
  <div class="media-label">Voluptas Sit Aspernatur <b>+</b></div>
</div>
<div class="media-card" style="left:770px">
  <div class="media-photo" role="img" aria-label="Photo of a doctor examining a seated patient" style="background:linear-gradient(120deg,#d7d0b4,#efeadc 50%,#8b8a7c)"></div>
  <div class="media-label">Voluptas Sit Aspernatur <b>+</b></div>
</div>

<!-- recent events -->
<section class="abs events" role="img" aria-label="Dim photo of a street scene with bicycles"></section>
<h2 class="abs display section-title" style="top:2030px;color:var(--white)">Recent Event</h2>
<article class="event-card" style="left:130px">
  <div class="event-photo" role="img" aria-label="Photo of a man using an adapted handbike on a grassy hill" style="background:linear-gradient(120deg,#6f9a4a,#a9c27d 50%,#9b2d2d)"></div>
  <div class="event-date">12<br>MAY</div>
  <h3 class="display event-title">Neque Porro Wuisquam</h3>
  <p class="event-text">Sed ut perspiciatis unde omnis iste natus error sit voluptatem accusantium</p>
  <div class="btn btn-readmore">Read more</div>
</article>
<article class="event-card" style="left:449px">
  <div class="event-photo" role="img" aria-label="Photo of people in wheelchairs gathered on a covered terrace" style="background:linear-gradient(120deg,#3b4a3e,#8a9c86 50%,#c8cfc8)"></div>
  <div class="event-date">12<br>MAY</div>
  <h3 class="display event-title">Neque Porro Wuisquam</h3>
  <p class="event-text">Sed ut perspiciatis unde omnis iste natus error sit voluptatem accusantium</p>
  <div class="btn btn-readmore">Read more</div>
</article>
<article class="event-card" style="left:770px">
  <div class="event-photo" role="img" aria-label="Photo of young athletes in sport wheelchairs on a court" style="background:linear-gradient(120deg,#5c7a58,#3c5a9a 50%,#b9b39a)"></div>
  <div class="event-date">12<br>MAY</div>
  <h3 class="display event-title">Neque Porro Wuisquam</h3>
  <p class="event-text">Sed ut perspiciatis unde omnis iste natus error sit voluptatem accusantium</p>
  <div class="btn btn-readmore">Read more</div>
</article>

<!-- contact -->
<section class="abs contact"></section>
<svg class="abs" style="left:130px;top:2604px" width="260" height="320" viewBox="130 2604 260 320">
  <defs><linearGradient id="cg" x1="0" y1="0" x2="1" y2="1"><stop offset="0" stop-color="#6fa043"/><stop offset=".5" stop-color="#e6c2a4"/><stop offset="1" stop-color="#3a2a52"/></linearGradient></defs>
  <polygon points="131,2690 388,2605 388,2921 131,2880" fill="url(#cg)" role="img" aria-label="Photo of a child blowing on a dandelion"/>
</svg>
<h2 class="abs display contact-title">Contact Us</h2>
<p class="abs contact-sub">Sed ut perspiciatis unde omnis iste natus error</p>
<div class="field" style="left:531px;top:2743px;width:228px;height:35px">Name:</div>
<div class="field" style="left:531px;top:2791px;width:228px;height:35px">Email:</div>
<div class="field" style="left:531px;top:2839px;width:228px;height:35px">Phone:</div>
<div class="field" style="left:764px;top:2743px;width:228px;height:83px">Comments:</div>
<div class="submit">SUBMIT</div>

<!-- footer -->
<svg class="abs" style="left:0;top:2870px" width="1200" height="463" viewBox="0 2870 1200 463">
  <polygon points="0,2926 472,3001 1200,2874 1200,3333 0,3333" fill="#2a2e33"/>
</svg>
<footer class="footer">
  <div class="wordmark"><span class="mark"></span><span>Open Paths<br>Association</span></div>
  <p class="abs footer-text footer-about">Sed ut perspiciatis unde omnis iste natus error sit voluptatem accusantium rem aperiam</p>
  <span class="abs footer-fb" aria-label="Social page"></span>

  <div class="abs condensed col-head" style="left:450px;top:3035px">Sitemap</div>
  <div class="abs col-links" style="left:450px;top:3064px">Home<br>Our Achivements<br>Media<br>Events<br>Contact Us</div>

  <div class="abs condensed col-head" style="left:670px;top:3035px">Others</div>
  <div class="abs col-links" style="left:670px;top:3064px">Privacy Policy<br>Terms &amp; Conditions<br>Leagal<br>Donate<br>Help / Support</div>

  <div class="abs condensed col-head" style="left:876px;top:3035px">Contacts</div>
  <div class="contact-row" style="top:3070px"><i></i><span>Chemin des Prés 12 / 1800<br>Valmont</span></div>
  <div class="contact-row" style="top:3110px"><i></i><span style="padding-top:3px">info@openpaths-association.example</span></div>

  <p class="abs copyright">Copyright © 2022 <span>Open Paths Association</span>. All Rights Reserved.</p>
</footer>

</body>
</html>
```